Machining Business Order Thank You Insert

I am looking for a business style card to include with orders that I ship. The card needs to thank the recipient for their order, and encourage them to leave a review. The card should include my business name and contact information and have an area to hand write a message.

I mainly sale on Craftlane and my own website. We are a machining an manufacturing business that are in the sale of mostly metal machined and 3d printed plastic products.

The front of the card should include the following:
Logo: (attached)
Snapgram: https://www.snapgram.example/kelvomill/
Friendsbook: https://www.friendsbook.example/KelvoMill
Website: https://www.kelvomill.example/

The back of the card needs an area to write a message

Industry/Entity Type

3D Printing, Machining, Craftlane

Contact Information for Business Card

Black or white front, white back to write a personal message

Font styles to use
Sans Serif

Colors

Designer to choose colors to be used in the design.

Requirements
Must have
• Encourage a review, social media info

```html
<!DOCTYPE html>
<html lang="en">
<head>
<meta charset="utf-8">
<title>KelvoMill – Order Thank You Insert</title>
<link rel="stylesheet" href="https://fonts.googleapis.com/css2?family=Great+Vibes&family=Lato:wght@400;700&display=swap">
<style>
  :root {
    --stage: #2c2c2c;
    --card-white: #ffffff;
    --card-black: #141414;
    --brand-orange: #f05a28;
    --brand-orange-deep: #d9441a;
    --brand-orange-soft: #f6906d;
    --ink-grey: #4a4a4a;
    --ink-white: #ffffff;
  }
  * { box-sizing: border-box; margin: 0; padding: 0; }
  html, body { width: 1200px; height: 900px; overflow: hidden; }
  body {
    background: var(--stage);
    font-family: "Lato", sans-serif;
    position: relative;
  }
  .card {
    position: absolute;
    left: 280px;
    width: 640px;
    height: 366px;
    box-shadow: 0 8px 24px rgba(0,0,0,.6);
  }
  .card--message { top: 52px; background: var(--card-white); }
  .card--thanks { top: 478px; background: var(--card-black); overflow: hidden; }

  .brand {
    position: absolute;
    display: flex;
    align-items: center;
    gap: 10px;
    font-family: "Lato", sans-serif;
    font-weight: 400;
    font-size: 15px;
    letter-spacing: .32em;
    text-transform: uppercase;
  }
  .brand__mark { width: 16px; height: 16px; border: 2px solid currentColor; }
  .card--message .brand { right: 40px; bottom: 60px; color: var(--ink-grey); }
  .card--thanks .brand { right: 34px; top: 176px; color: var(--ink-white); }

  .thanks-frame { position: absolute; left: 40px; top: 34px; width: 460px; height: 180px; }
  .thanks-text {
    position: absolute;
    left: 120px; top: 76px;
    width: 320px;
    text-align: center;
    font-family: "Great Vibes", cursive;
    font-size: 62px;
    line-height: 1.2;
    color: var(--ink-grey);
    transform: rotate(-6deg);
  }

  .review-ask {
    position: absolute;
    left: 44px; top: 228px;
    color: var(--brand-orange);
    font-size: 16px;
    font-weight: 700;
    line-height: 1.3;
  }

  .contact-list {
    position: absolute;
    left: 44px; bottom: 26px;
    list-style: none;
    color: var(--ink-white);
    font-size: 17px;
    line-height: 1.55;
  }
  .contact-list li { display: flex; align-items: center; gap: 10px; }
  .contact-icon { width: 20px; height: 20px; flex: none; }
</style>
</head>
<body>

  <section class="card card--message" aria-label="Card back with space for a handwritten message">
    <div class="brand"><span class="brand__mark"></span>KelvoMill</div>
  </section>

  <section class="card card--thanks" aria-label="Card front">
    <svg class="thanks-frame" viewBox="0 0 460 180" aria-hidden="true">
      <polygon points="4,176 150,6 456,6 310,176" fill="none" stroke="var(--brand-orange-soft)" stroke-width="6" stroke-linejoin="round" opacity=".6"/>
      <polygon points="16,170 156,14 444,14 304,170" fill="none" stroke="var(--brand-orange-soft)" stroke-width="3" stroke-linejoin="round"/>
      <polygon points="30,162 164,24 430,24 296,162" fill="var(--card-white)" stroke="var(--brand-orange-deep)" stroke-width="4" stroke-linejoin="round"/>
    </svg>
    <p class="thanks-text">Thank you!</p>

    <div class="brand"><span class="brand__mark"></span>KelvoMill</div>

    <p class="review-ask">Enjoying your order? Please leave us a review!</p>

    <ul class="contact-list">
      <li>
        <svg class="contact-icon" viewBox="0 0 20 20" aria-hidden="true">
          <circle cx="10" cy="10" r="8.5" fill="none" stroke="#fff" stroke-width="1.5"/>
          <ellipse cx="10" cy="10" rx="4" ry="8.5" fill="none" stroke="#fff" stroke-width="1.2"/>
          <line x1="1.5" y1="10" x2="18.5" y2="10" stroke="#fff" stroke-width="1.2"/>
          <line x1="3" y1="6" x2="17" y2="6" stroke="#fff" stroke-width="1"/>
          <line x1="3" y1="14" x2="17" y2="14" stroke="#fff" stroke-width="1"/>
        </svg>
        www.kelvomill.example
      </li>
      <li>
        <svg class="contact-icon" viewBox="0 0 20 20" aria-hidden="true"><circle cx="10" cy="10" r="9" fill="#fff"/></svg>
        www.snapgram.example/kelvomill
      </li>
      <li>
        <svg class="contact-icon" viewBox="0 0 20 20" aria-hidden="true"><circle cx="10" cy="10" r="9" fill="#fff"/></svg>
        www.friendsbook.example/KelvoMill
      </li>
    </ul>
  </section>

</body>
</html>
```